5 website banners (slides show)

We need 5 website sliding banners created for a website all about internet safety. The topics for each banner are:

Cyberbullying
Fraud
seniors
social networking

Sizes: 953 pixels x 281 pixels

I have stock images to use or feel free to use your own or one I can purchase from pixelharbor.example.

Industry/Entity Type

Internet

```html
<!DOCTYPE html>
<html lang="en">
<head>
<meta charset="utf-8">
<title>SafeWave – Online Safety and Security</title>
<link rel="stylesheet" href="https://fonts.googleapis.com/css2?family=Ubuntu:ital,wght@0,400;0,500;0,700;1,500&display=swap">
<style>
  :root {
    --pink: #e8088a;
    --pink-dark: #9c0a5e;
    --green: #8ccb2f;
    --green-mid: #73b228;
    --green-dark: #4f8c1a;
    --green-light: #a6dc4a;
    --nav-divider: #9ad25a;
    --text-grey: #8a949a;
    --link-lilac: #b466c8;
    --social-blue: #3b5a98;
    --badge-rim: #8fa3b8;
    --badge-face: #4a86c8;
    --panel-shadow: #d9d9d9;
    --white: #ffffff;
  }
  * { box-sizing: border-box; margin: 0; padding: 0; }
  html, body { width: 1200px; height: 814px; overflow: hidden; background: var(--white); }
  body { position: relative; font-family: Arial, Helvetica, sans-serif; }
  .display { font-family: 'Ubuntu', Arial, sans-serif; font-weight: 500; white-space: nowrap; }

  .utility-bar {
    position: absolute; left: 150px; top: 18px; width: 604px; height: 31px;
    background: var(--pink); border-radius: 5px 0 0 5px;
    display: flex; align-items: center; padding-left: 14px; gap: 24px;
  }
  .utility-bar a { color: var(--white); font-size: 12.5px; text-decoration: none; }
  .social-square {
    position: absolute; left: 726px; top: 22px; width: 23px; height: 23px;
    background: var(--social-blue); border-radius: 2px;
  }
  .search {
    position: absolute; left: 754px; top: 18px; width: 294px; height: 31px;
    border: 1px solid #e8eef2; background: var(--white);
    font-size: 12px; color: #8a959c; padding: 8px 10px;
  }
  .search-button {
    position: absolute; left: 1019px; top: 21px; width: 26px; height: 25px;
    background: var(--pink); border-radius: 3px;
  }

  .brand { position: absolute; left: 166px; top: 64px; width: 400px; height: 100px; }
  .brand-mark { width: 96px; height: 96px; border-radius: 50%; background: var(--pink); border: 5px solid #f8c7e2; }
  .brand-name {
    position: absolute; left: 106px; top: 10px;
    font-size: 52px; line-height: 56px; color: var(--pink); letter-spacing: -0.5px;
  }
  .brand-tagline {
    position: absolute; left: 108px; top: 68px;
    font-size: 12px; color: var(--green-mid); letter-spacing: -0.2px;
  }

  .report {
    position: absolute; left: 711px; top: 71px; width: 337px; height: 91px;
    background: linear-gradient(180deg, var(--green-light), var(--green-mid));
    border-radius: 3px; color: var(--white);
  }
  .report::after {
    content: ""; position: absolute; left: 7px; top: 7px; right: 7px; bottom: 7px;
    border: 1px dashed rgba(255,255,255,0.7);
  }
  .report-title { position: absolute; left: 16px; top: 15px; font-size: 19px; letter-spacing: -0.3px; }
  .report-click { position: absolute; left: 176px; top: 40px; font-size: 11.5px; }
  .report-phone { position: absolute; left: 13px; top: 55px; font-size: 22px; letter-spacing: -0.4px; }
  .report-badge { position: absolute; right: 10px; top: 4px; width: 56px; height: 82px; }

  .main-nav {
    position: absolute; left: 150px; top: 179px; width: 900px; height: 63px;
    background: var(--green-mid); border-radius: 5px;
  }
  .main-nav ul { list-style: none; display: flex; height: 52px; }
  .main-nav li {
    display: flex; align-items: center; justify-content: center;
    border-right: 2px solid var(--nav-divider);
    font-size: 14px; color: var(--white); letter-spacing: -0.2px;
  }
  .main-nav li.is-current { background: var(--green); border-right: none; border-radius: 5px 0 0 0; }

  .hero {
    position: absolute; left: 150px; top: 253px; width: 900px; height: 265px;
    background: radial-gradient(ellipse at 55% 35%, #e0128c 0%, #c60a7b 45%, #8c0956 100%);
    border: 2px solid #a40a66; overflow: hidden;
  }
  .hero-title {
    position: absolute; left: 19px; top: 72px;
    font-size: 42px; color: var(--white); letter-spacing: -0.5px;
    text-shadow: 1px 2px 3px rgba(0,0,0,0.35);
  }
  .hero-subtitle {
    position: absolute; left: 21px; top: 120px;
    font-style: italic; font-size: 33px; color: var(--white);
    text-shadow: 1px 2px 3px rgba(0,0,0,0.35); letter-spacing: -0.5px;
  }
  .hero-button {
    position: absolute; left: 26px; top: 177px; width: 181px; height: 43px;
    background: var(--green); display: flex; color: var(--white); font-size: 17px;
  }
  .hero-button span { flex: 1; display: flex; align-items: center; padding-left: 14px; letter-spacing: -0.3px; }
  .hero-button i { width: 46px; background: var(--green-dark); display: flex; align-items: center; justify-content: center; }
  .hero-photo {
    position: absolute; left: 436px; top: 22px; width: 460px; height: 235px;
    background: radial-gradient(ellipse at 50% 55%, rgba(240,210,200,0.55), rgba(120,140,190,0.35) 55%, rgba(200,10,120,0) 75%);
  }

  .issues {
    position: absolute; left: 150px; top: 528px; width: 208px; height: 300px;
    background: var(--green); border-radius: 7px 7px 0 0; padding: 10px;
  }
  .issues-frame { border: 1px dashed rgba(255,255,255,0.8); height: 100%; border-radius: 4px; padding: 18px 0 0 10px; }
  .issues h2 { font-size: 14.5px; color: var(--white); margin-bottom: 11px; }
  .issues ul { list-style: none; padding-left: 5px; }
  .issues li { font-size: 12px; color: var(--white); height: 23.5px; }

  .welcome {
    position: absolute; left: 376px; top: 528px; width: 670px; height: 300px;
    border-right: 4px solid var(--panel-shadow); border-radius: 0 7px 0 0;
  }
  .welcome h1 { position: absolute; left: 10px; top: 20px; font-size: 25px; color: var(--pink); letter-spacing: -0.3px; }
  .edit-list { position: absolute; left: 10px; top: 56px; font-size: 11.5px; color: var(--link-lilac); list-style: none; }
  .edit-list li::before { content: "•"; color: #999; margin-right: 10px; }
  .welcome p {
    position: absolute; left: 10px; width: 650px;
    font-size: 11.6px; line-height: 16px; color: var(--text-grey);
  }
  .audience { position: absolute; top: 262px; font-size: 15px; color: var(--pink); }
</style>
</head>
<body>
  <nav class="utility-bar"><a>Home</a><a>FAQs</a><a>Contact</a></nav>
  <div class="social-square" aria-label="Social page"></div>
  <div class="search">Search...</div>
  <div class="search-button">
    <svg width="26" height="25" viewBox="0 0 26 25"><circle cx="12" cy="11" r="6" fill="none" stroke="#fff" stroke-width="2.5"/><line x1="16" y1="15" x2="21" y2="20" stroke="#fff" stroke-width="3" stroke-linecap="round"/></svg>
  </div>

  <header class="brand">
    <div class="brand-mark"></div>
    <div class="brand-name display">SAFEWAVE</div>
    <div class="brand-tagline display">ISLAND ONLINE SAFETY AND SECURITY</div>
  </header>

  <div class="report">
    <div class="report-title display">REPORT A CYBERCRIME</div>
    <div class="report-click display">CLICK HERE</div>
    <div class="report-phone display">or call 1-555-010-4477</div>
    <svg class="report-badge" viewBox="0 0 60 84"><path d="M6 10 L30 2 L56 10 L54 48 Q50 70 30 82 Q10 70 6 48 Z" fill="var(--badge-rim)" stroke="#dfe6ee" stroke-width="3"/><path d="M12 16 L30 10 L50 16 L48 48 Q45 64 30 74 Q15 64 12 48 Z" fill="var(--badge-face)"/></svg>
  </div>

  <nav class="main-nav">
    <ul class="display">
      <li class="is-current" style="width:76px">HOME</li>
      <li style="width:81px">ABOUT</li>
      <li style="width:128px">FOR PARENTS</li>
      <li style="width:111px">FOR TEENS</li>
      <li style="width:125px">FOR TWEENS</li>
      <li style="width:97px">FOR KIDS</li>
      <li style="width:137px">FOR TEACHERS</li>
      <li style="width:115px">RESOURCES</li>
    </ul>
  </nav>

  <section class="hero">
    <div class="hero-title display">SENIORS</div>
    <div class="hero-subtitle display">Talk about the digital world</div>
    <div class="hero-button display"><span>LEARN MORE</span><i><svg width="18" height="14" viewBox="0 0 18 14"><path d="M2 12 Q4 5 11 5 L11 1 L17 7 L11 12 L11 8.5 Q6 8.5 2 12 Z" fill="#fff"/></svg></i></div>
    <div class="hero-photo" role="img" aria-label="Photo of a family lying on the floor around a laptop"></div>
  </section>

  <aside class="issues">
    <div class="issues-frame">
      <h2 class="display">CHOOSE AN ISSUE</h2>
      <ul>
        <li>Cyberbullying</li><li>Sexting</li><li>Internet Safety</li><li>Fraud</li><li>Mobile Devices</li>
        <li>Gangs</li><li>Blogging</li><li>Predators</li><li>Copywriting</li><li>Social Networking</li>
      </ul>
    </div>
  </aside>

  <main class="welcome">
    <h1 class="display">WELCOME</h1>
    <ul class="edit-list"><li>Edit</li></ul>
    <p style="top:93px">Welcome to SafeWave, the island's source of information on internet safety, brought to you by the Department of Digital Affairs. Our aim is to provide practical tips, resources and contact information to help parents, children and educators to use the Internet safely and be on guard against online predators and other inappropriate online content.</p>
    <p style="top:161px">By knowing the dangers and how to avoid them, you can take advantage of all the positive aspects of the Internet while avoiding most of its pitfalls.</p>
    <p style="top:213px">The Department of Digital Affairs partners with the Island Constabulary, Northwind Software, Kestrel's Corner and a number of other organizations locally and internationally to bring innovative and media rich educational tools to the island</p>
    <div class="audience display" style="left:0">KIDS</div>
    <div class="audience display" style="left:223px">TWEENS</div>
    <div class="audience display" style="left:445px">TEENS</div>
  </main>
</body>
</html>
```